Luxury Business Card Design for High-End Window Treatments

Gilded Slatworks
Custom Plantation Shutters & Architectural Shading Systems

⸻

BACK

Daniel Trevick
Owner

Custom Interior & Exterior Window Treatments

919-555-0148
gildedslatworks.com

I have included a picture that I’m hoping we can use on the back, but I’m also wondering if you can get rid of the ladder? Should we get rid of shutters , shades and blinds underneath Gilded Slatworks?

Target Market(s)

High-end residential homeowners, custom home builders, architects, interior designers, and luxury renovation clients seeking premium plantation shutters and motorized architectural shading systems.

Industry/Entity Type

Custom Window treatments

Contact Information for Business Card

Front Gilded Slatworks Custom Plantation Shutters Motorized Architectural Shading Systems BACK Daniel Trevick Owner 919-555-0148 GildedSlatworks.com Custom Interior & Exterior Window Treatments By Appointment

Requirements
Nice to have
• Not 100% sure on nice to halves or the color but you can definitely check out my website to get a better understanding of what I’m trying to do

```html
<!DOCTYPE html>
<html lang="en">
<head>
<meta charset="utf-8">
<title>Gilded Slatworks – Business Card</title>
<link href="https://fonts.googleapis.com/css2?family=Raleway:wght@300;400;600;700;800&display=swap" rel="stylesheet">
<style>
  :root {
    --stage: #3a3b3e;
    --card: #26282c;
    --card-edge: #2e3035;
    --gold: #c2a052;
    --gold-light: #e0c172;
    --gold-dark: #8f7032;
    --white: #ffffff;
    --sky: #8fb6e6;
    --foliage: #5d6b44;
    --house: #6f747c;
  }
  * { margin: 0; padding: 0; box-sizing: border-box; }
  html, body { width: 1200px; height: 758px; overflow: hidden; }
  body {
    background: var(--stage);
    font-family: "Raleway", Arial, sans-serif;
    position: relative;
  }
  .card {
    position: absolute;
    top: 222px;
    width: 548px;
    height: 313px;
    border-radius: 18px;
    background: linear-gradient(135deg, var(--card-edge), var(--card) 60%);
    overflow: hidden;
    box-shadow: 0 14px 30px rgba(0,0,0,0.35);
  }
  .card-front { left: 36px; }
  .card-back { left: 616px; }

  /* Front */
  .accent-bar {
    position: absolute;
    width: 14px;
    background: linear-gradient(180deg, var(--gold-dark) 0 50%, var(--gold-light) 50% 100%);
  }
  .accent-bar-top { right: 0; top: 56px; height: 120px; }
  .accent-bar-bottom { left: 0; top: 168px; height: 118px; }
  .front-wordmark {
    position: absolute;
    left: 0; right: 0; top: 86px;
    text-align: center;
    color: var(--gold);
    font-weight: 600;
    font-size: 54px;
    line-height: 1.1;
    letter-spacing: 0.5px;
  }
  .front-wordmark span { display: block; }
  .front-wordmark .line-two { padding-left: 90px; }

  /* Back */
  .back-art { position: absolute; inset: 0; }
  .back-wordmark {
    position: absolute;
    left: 318px; top: 22px;
    color: var(--gold);
    font-weight: 600;
    font-size: 27px;
    line-height: 1.05;
  }
  .back-wordmark span { display: block; }
  .back-wordmark .line-two { padding-left: 30px; }
  .name-block {
    position: absolute;
    right: 22px; top: 104px;
    text-align: right;
    color: var(--white);
  }
  .person-name { font-weight: 800; font-size: 27px; line-height: 1; }
  .person-role { font-weight: 400; font-size: 13px; margin-top: 3px; letter-spacing: 0.5px; }
  .tagline {
    position: absolute;
    right: 22px; top: 184px;
    text-align: right;
    color: var(--white);
    font-weight: 700;
    font-size: 14px;
    line-height: 1.3;
  }
  .contact-list {
    position: absolute;
    right: 22px; top: 236px;
    list-style: none;
    color: var(--white);
    font-weight: 300;
    font-size: 14px;
    line-height: 1.55;
  }
  .contact-item { display: flex; align-items: center; justify-content: flex-end; gap: 7px; }
  .contact-icon { width: 12px; height: 12px; }
</style>
</head>
<body>

<section class="card card-front" aria-label="Business card front">
  <div class="accent-bar accent-bar-top"></div>
  <div class="accent-bar accent-bar-bottom"></div>
  <h1 class="front-wordmark">
    <span class="line-one">Gilded</span>
    <span class="line-two">Slatworks</span>
  </h1>
</section>

<section class="card card-back" aria-label="Business card back">
  <svg class="back-art" width="548" height="313" viewBox="0 0 548 313">
    <defs>
      <linearGradient id="photoTone" x1="0" y1="0" x2="0" y2="1">
        <stop offset="0" stop-color="var(--sky)"/>
        <stop offset="0.45" stop-color="var(--house)"/>
        <stop offset="1" stop-color="var(--foliage)"/>
      </linearGradient>
      <linearGradient id="bandGold" x1="0" y1="0" x2="1" y2="0">
        <stop offset="0" stop-color="var(--gold-dark)"/>
        <stop offset="0.6" stop-color="var(--gold)"/>
        <stop offset="1" stop-color="var(--gold-light)"/>
      </linearGradient>
    </defs>
    <polygon role="img" aria-label="Photo of a home's screened porch fitted with exterior shades, under a blue sky with pine trees"
             points="100,0 290,0 255,313 65,313" fill="url(#photoTone)"/>
    <line x1="100" y1="0" x2="65" y2="313" stroke="var(--gold)" stroke-width="3"/>
    <line x1="291" y1="0" x2="256" y2="313" stroke="var(--gold)" stroke-width="4"/>
    <polygon class="name-band" points="283,98 548,98 548,162 276,162" fill="url(#bandGold)"/>
  </svg>

  <h2 class="back-wordmark">
    <span class="line-one">Gilded</span>
    <span class="line-two">Slatworks</span>
  </h2>

  <div class="name-block">
    <p class="person-name">Daniel Trevick</p>
    <p class="person-role">Owner</p>
  </div>

  <p class="tagline">Custom Interior &amp; Exterior<br>Window Treatments</p>

  <ul class="contact-list">
    <li class="contact-item">919-555-0148
      <svg class="contact-icon" viewBox="0 0 24 24" aria-hidden="true"><path fill="var(--gold)" d="M6.6 10.8a15 15 0 0 0 6.6 6.6l2.2-2.2a1 1 0 0 1 1-.25 11.4 11.4 0 0 0 3.6.57 1 1 0 0 1 1 1V20a1 1 0 0 1-1 1A17 17 0 0 1 3 4a1 1 0 0 1 1-1h3.5a1 1 0 0 1 1 1c0 1.25.2 2.45.57 3.57a1 1 0 0 1-.25 1z"/></svg>
    </li>
    <li class="contact-item">gildedslatworks.com
      <svg class="contact-icon" viewBox="0 0 24 24" aria-hidden="true"><circle cx="12" cy="12" r="10" fill="none" stroke="var(--gold)" stroke-width="2.4"/><path d="M2 12h20M12 2c3 3 3 17 0 20M12 2c-3 3-3 17 0 20" fill="none" stroke="var(--gold)" stroke-width="1.8"/></svg>
    </li>
  </ul>
</section>

</body>
</html>
```